Want a package created for a new protein bar

We would like a new package created for a new protein bar project The name of the bar will be VORNBar a real food protein bar, we would like a ‘window’ on the package of bar like Bold Meadow bar below in images.

VORNBar
‘Super Food Bar’
14g of Whey Protein
The package film size is the following 12cm width x 15cm Length,
Flavor Peanut Chocolate Chip, additional information will be attached shortly like nutrition facts,

Target Market(s)

fitness market, bodybuilders, athletes, everyday people

Industry/Entity Type

Health Product

Logo Text

VORNBar

Font styles to use
Serif
Sans Serif
Decorative

Requirements
Must have
• Package window

```html
<!DOCTYPE html>
<html lang="en">
<head>
<meta charset="utf-8">
<title>VORNBar – Peanut Chocolate Chip Wrapper</title>
<link rel="stylesheet" href="https://fonts.googleapis.com/css2?family=Didact+Gothic&display=swap">
<style>
  :root {
    --backdrop: #cbbda9;
    --film-white: #f4f4f2;
    --film-shade: #e2e2e0;
    --band-peanut: #c98608;
    --band-peanut-deep: #b5760a;
    --band-fresh: #11b511;
    --band-fresh-deep: #049c04;
    --ink: #111111;
    --rule-grey: #a9a9a9;
    --window-light: #d9a86a;
    --window-mid: #a8703c;
    --window-dark: #4a2a16;
  }
  html, body {
    margin: 0;
    padding: 0;
    width: 1116px;
    height: 1200px;
    overflow: hidden;
    background: var(--backdrop);
  }
  .wrapper-lineup {
    width: 1116px;
    height: 1200px;
    display: flex;
    justify-content: center;
    align-items: center;
    gap: 70px;
  }
  .wrapper {
    width: 420px;
    height: 1092px;
    display: block;
  }
  .film { fill: var(--film-white); }
  .film-shade { fill: var(--film-shade); }
  .wrapper--peanut .flavour-band { fill: var(--band-peanut); }
  .wrapper--peanut .flavour-band-deep { fill: var(--band-peanut-deep); }
  .wrapper--fresh .flavour-band { fill: var(--band-fresh); }
  .wrapper--fresh .flavour-band-deep { fill: var(--band-fresh-deep); }
  .window-swoosh { fill: var(--ink); }
  .window-rule { fill: none; stroke: var(--rule-grey); stroke-width: 3; }
  .brand-name {
    font-family: "Didact Gothic", sans-serif;
    font-size: 60px;
    fill: var(--ink);
    letter-spacing: 1px;
  }
  .tagline {
    font-family: "Didact Gothic", sans-serif;
    font-size: 27px;
    fill: var(--ink);
  }
  .protein-claim {
    font-family: "Didact Gothic", sans-serif;
    font-size: 34px;
    fill: var(--ink);
  }
</style>
</head>
<body>
<main class="wrapper-lineup">

  <svg class="wrapper wrapper--peanut" viewBox="0 0 400 1040" aria-label="VORNBar wrapper, peanut colourway">
    <defs>
      <clipPath id="peanut-outline">
        <path d="M10,60 l20,-20 l20,20 l20,-20 l20,20 l20,-20 l20,20 l20,-20 l20,20 l20,-20 l20,20 l20,-20 l20,20 l20,-20 l20,20 l20,-20 l20,20 l20,-20 l20,20 l20,-20 Q380,130 360,170 L360,870 Q372,930 390,980 l-20,20 l-20,-20 l-20,20 l-20,-20 l-20,20 l-20,-20 l-20,20 l-20,-20 l-20,20 l-20,-20 l-20,20 l-20,-20 l-20,20 l-20,-20 l-20,20 l-20,-20 l-20,20 l-20,-20 l-20,20 Q28,930 40,870 L40,170 Q20,130 10,60 Z"/>
      </clipPath>
      <linearGradient id="peanut-window-fill" x1="0" y1="0" x2="1" y2="1">
        <stop offset="0" stop-color="var(--window-mid)"/>
        <stop offset="0.45" stop-color="var(--window-light)"/>
        <stop offset="0.75" stop-color="var(--window-dark)"/>
        <stop offset="1" stop-color="var(--window-mid)"/>
      </linearGradient>
      <radialGradient id="peanut-cookie-fill">
        <stop offset="0" stop-color="#c59a66"/>
        <stop offset="1" stop-color="#8a5a32"/>
      </radialGradient>
    </defs>
    <g clip-path="url(#peanut-outline)">
      <rect class="film" x="0" y="0" width="400" height="1040"/>
      <rect class="film-shade" x="0" y="860" width="220" height="180"/>
      <rect class="flavour-band" x="218" y="390" width="200" height="650"/>
      <rect class="flavour-band-deep" x="218" y="870" width="200" height="170"/>
      <path class="window-rule" d="M30,330 Q200,420 370,380"/>
      <path class="window-rule" d="M30,345 Q200,440 370,398"/>
      <path class="window-swoosh" d="M100,330 Q230,370 370,320 L370,345 Q240,395 100,330 Z"/>
      <path role="img" aria-label="Window showing the peanut chocolate chip bar inside" fill="url(#peanut-window-fill)" d="M0,0 L400,0 L400,300 Q330,370 220,365 Q110,360 0,300 Z"/>
    </g>
    <g role="img" aria-label="Illustration of chocolate chip cookies">
      <ellipse cx="130" cy="500" rx="62" ry="80" fill="url(#peanut-cookie-fill)"/>
    </g>
    <text class="brand-name" transform="translate(290,410) rotate(90)">VORNBar</text>
    <text class="tagline" transform="translate(242,650) rotate(90)">‘Super Food Bar’</text>
    <text class="protein-claim" transform="translate(175,660) rotate(90)">14g of</text>
    <text class="protein-claim" transform="translate(135,610) rotate(90)">Whey Protein</text>
  </svg>

  <svg class="wrapper wrapper--fresh" viewBox="0 0 400 1040" aria-label="VORNBar wrapper, green colourway">
    <defs>
      <clipPath id="fresh-outline">
        <path d="M10,60 l20,-20 l20,20 l20,-20 l20,20 l20,-20 l20,20 l20,-20 l20,20 l20,-20 l20,20 l20,-20 l20,20 l20,-20 l20,20 l20,-20 l20,20 l20,-20 l20,20 l20,-20 Q380,130 360,170 L360,870 Q372,930 390,980 l-20,20 l-20,-20 l-20,20 l-20,-20 l-20,20 l-20,-20 l-20,20 l-20,-20 l-20,20 l-20,-20 l-20,20 l-20,-20 l-20,20 l-20,-20 l-20,20 l-20,-20 l-20,20 l-20,-20 l-20,20 Q28,930 40,870 L40,170 Q20,130 10,60 Z"/>
      </clipPath>
      <linearGradient id="fresh-window-fill" x1="0" y1="0" x2="1" y2="1">
        <stop offset="0" stop-color="var(--window-mid)"/>
        <stop offset="0.45" stop-color="var(--window-light)"/>
        <stop offset="0.75" stop-color="var(--window-dark)"/>
        <stop offset="1" stop-color="var(--window-mid)"/>
      </linearGradient>
      <radialGradient id="fresh-cookie-fill">
        <stop offset="0" stop-color="#c59a66"/>
        <stop offset="1" stop-color="#8a5a32"/>
      </radialGradient>
    </defs>
    <g clip-path="url(#fresh-outline)">
      <rect class="film" x="0" y="0" width="400" height="1040"/>
      <rect class="film-shade" x="0" y="860" width="220" height="180"/>
      <rect class="flavour-band" x="218" y="390" width="200" height="650"/>
      <rect class="flavour-band-deep" x="218" y="870" width="200" height="170"/>
      <path class="window-rule" d="M30,330 Q200,420 370,380"/>
      <path class="window-rule" d="M30,345 Q200,440 370,398"/>
      <path class="window-swoosh" d="M100,330 Q230,370 370,320 L370,345 Q240,395 100,330 Z"/>
      <path role="img" aria-label="Window showing the peanut chocolate chip bar inside" fill="url(#fresh-window-fill)" d="M0,0 L400,0 L400,300 Q330,370 220,365 Q110,360 0,300 Z"/>
    </g>
    <g role="img" aria-label="Illustration of chocolate chip cookies">
      <ellipse cx="130" cy="500" rx="62" ry="80" fill="url(#fresh-cookie-fill)"/>
    </g>
    <text class="brand-name" transform="translate(290,410) rotate(90)">VORNBar</text>
    <text class="tagline" transform="translate(242,650) rotate(90)">‘Super Food Bar’</text>
    <text class="protein-claim" transform="translate(175,660) rotate(90)">14g of</text>
    <text class="protein-claim" transform="translate(135,610) rotate(90)">Whey Protein</text>
  </svg>

</main>
</body>
</html>
```